Online Dating Website called WinkAtWheel.com

PLEASE CAN ALL PARTICIPATING DESIGNERS PLEASE SUBMIT ALL PAGES AS DETAILED IN THE ORIGINAL BRIEF BELOW WITHIN 48 HOURS TO AVOID WINKATWHEEL EXTENDING THE CONTEST FURTHER.

We have an online dating website that is 95% fully functional and now require an exciting and creative designer to help us create the best dating experience. We are looking for your ideas on a couple of our key pages. These are our landing, profile and search page. We already have a homepage that we are happy with and winning designers will look to build upon the foundations of the homepage and extend them through their designs.

The premise of the site is the idea that if you've ever seen someone out driving and wished you could communicate because you found them attractive, how would you? Well with WinkAtWheel.com you can. Just enter their vehicle registration number (license plate) in to the website in order to get in touch, flirt and develop a relationship. It also allows users to find each other based on other criteria. It acts as both a specialist service and a normal dating website.

The pages that require developing are 1) our landing page, this is the page users see when they first login to the site, it comprises various pieces of information but it's primary function is a live feed of events generated based on the users favourited profiles and interactions with the user. 2) The profile page is the page where users can edit their own information, given the nature of this page we are looking for a creative design that gives this page some flair. 3) Finally we are looking for ideas for our search page, this page needs to provide a list of users who meet the user's search requirements and display the profile of a selected user.
Updates

Project Deadline Extended
Reason: We've asked for certain pages in our brief to be designed and this still hasn't been done. We've contacted the designers that have currently submitted designs and requested this several times. We still await for this to happen.

Target Market(s)

Male or Female age 18+

Industry/Entity Type

Dating

Requirements
Must have
• Our must have feature is a designer with an open mind. The functionality of the site must be present, all we ask is for you to be creative with the layout. Think out side of the box, change the colours, the layout, and the background as you feel. Make it look current and appealing to the user.
Nice to have
• Theme's carried through from the home page
Should not have
• Do not include Comic Sans or Times New Roman font in your designs.

```html
<!DOCTYPE html>
<html lang="en">
<head>
<meta charset="utf-8">
<title>winkatwheel – Home</title>
<link href="https://fonts.googleapis.com/css2?family=Source+Sans+3:wght@400;600;700&display=swap" rel="stylesheet">
<style>
:root{
  --dark:#363636;--dark2:#2c2c2c;--page:#ffffff;--line:#e2e2e2;
  --blue:#1b9fdc;--blue2:#0f86c6;--pink:#ec3f8f;--pink2:#d9267a;
  --green:#83c41f;--green2:#5fa312;--orange:#ffa200;--orange2:#f58400;
  --cyan:#00bede;--lime:#a7c715;--text:#8a8a8a;--title:#4a4a4a;
}
*{box-sizing:border-box;margin:0;padding:0}
html,body{width:779px;height:1200px;overflow:hidden;background:var(--page);font-family:"Source Sans 3",sans-serif;color:var(--text)}
.canvas{position:relative;width:779px;height:1200px}
.abs{position:absolute}
.topbar{left:0;top:0;width:779px;height:72px;background:var(--dark)}
.brand{left:60px;top:20px;color:#fff;font-size:22px;font-weight:400;letter-spacing:.2px;display:flex;align-items:center;gap:8px}
.brand i{display:inline-block;width:12px;height:12px;border-radius:50%;background:var(--pink)}
.nav{left:280px;top:26px;display:flex;align-items:center;font-size:12px;color:#fff}
.nav a{color:#fff;text-decoration:none;padding:0 7px}
.nav .sep{color:#aaa}
.nav .on{background:#222;border-radius:14px;padding:7px 13px;margin-right:8px}
.box{background:#fff;border:1px solid var(--line);border-radius:5px;box-shadow:0 1px 2px rgba(0,0,0,.08);overflow:hidden}
.boxhead{height:27px;line-height:27px;padding-left:14px;color:#fff;font-size:13px}
.hb{background:linear-gradient(var(--blue),var(--blue2))}
.hg{background:linear-gradient(var(--green),var(--green2))}
.photo{border-radius:4px}
.field{position:absolute;left:11px;width:116px;height:20px;border:1px solid #ddd;border-radius:2px;font-size:8px;line-height:18px;padding-left:9px;color:#777;background:#fff}
.caret{position:absolute;right:6px;top:7px;border:4px solid transparent;border-top-color:#888}
.btn{position:absolute;height:15px;border-radius:2px;color:#fff;font-size:7.5px;line-height:15px;text-align:center}
.feature{text-align:center;border-radius:6px;overflow:hidden;background:#fff;border:1px solid var(--line);box-shadow:0 1px 2px rgba(0,0,0,.08)}
.feature .top{height:74px;border-bottom-left-radius:50% 14px;border-bottom-right-radius:50% 14px;display:flex;align-items:center;justify-content:center}
.feature h3{font-size:14px;font-weight:600;margin-top:11px}
.feature p{font-size:7.3px;line-height:11.5px;margin:6px 12px 0}
.fav{position:absolute;left:14px;width:110px;height:48px}
.fav .photo{position:absolute;left:0;top:2px;width:45px;height:43px}
.fav b{position:absolute;left:52px;top:4px;font-size:8px;color:var(--title);font-weight:600}
.fav span{position:absolute;left:52px;font-size:7px;color:#999}
.favline{position:absolute;left:0;width:136px;border-top:1px solid #eee}
.post{position:absolute;left:205px;width:372px;height:108px}
.post .card{position:absolute;left:1px;top:14px;width:370px;height:94px;background:#fff;border:1px solid var(--line);border-radius:6px;box-shadow:0 1px 2px rgba(0,0,0,.07)}
.post .head{position:absolute;left:0;top:0;width:372px;height:29px;border-radius:7px;color:#fff;font-size:13px;line-height:29px;padding-left:14px;box-shadow:0 1px 2px rgba(0,0,0,.15)}
.post .photo{position:absolute;left:16px;top:40px;width:58px;height:57px}
.post p{position:absolute;left:84px;top:42px;width:270px;font-size:8.2px;line-height:14.5px;color:#8a8a8a}
.post .meta{position:absolute;left:85px;top:77px;font-size:8.2px;color:#555;font-weight:600;display:flex;align-items:center;gap:6px}
.bubble{width:14px;height:9px;background:#444;border-radius:4px;position:relative}
.bubble:after{content:"";position:absolute;left:2px;bottom:-3px;border:3px solid transparent;border-top-color:#444;border-left-color:#444}
.pink{background:linear-gradient(var(--pink),var(--pink2))}
.green{background:linear-gradient(var(--green),var(--green2))}
.orange{background:linear-gradient(var(--orange),var(--orange2))}
.blue{background:linear-gradient(var(--blue),var(--blue2))}
.pager{left:207px;top:1041px;width:376px;height:25px;background:#f1f1f1;border:1px solid #e4e4e4;border-radius:3px;font-size:8.5px;color:#555}
.pager .lbl{position:absolute;left:14px;top:7px}
.pager .pages{position:absolute;right:16px;top:5px;display:flex;gap:7px;align-items:center}
.pager .cur{background:#333;color:#fff;border-radius:2px;padding:1px 4px}
.mlist{position:absolute;left:12px;top:38px;font-size:7.3px;color:#666;list-style:none}
.mlist li{height:18.4px;line-height:18.4px}
.mlist li:before{content:"›";color:#999;margin-right:5px}
.mlist b{color:var(--blue2);font-weight:700;font-size:8px}
.match{position:absolute;width:56px;text-align:center;font-size:7.5px;color:#555;line-height:11px}
.match .photo{width:56px;height:54px;border:1px solid #ddd;border-radius:2px;margin-bottom:2px}
.match em{font-style:normal;color:var(--blue2);font-size:8.5px}
.match.dark{background:#2f2f2f;color:#fff;border-radius:3px;padding-bottom:4px}
.match.dark em{color:#6ac6ff}
.chat{left:746px;top:272px;width:33px;height:115px;background:var(--dark);border-radius:4px 0 0 4px;color:#fff}
.chat span{position:absolute;left:6px;top:80px;transform:rotate(-90deg);transform-origin:0 0;font-size:12px;font-weight:700;white-space:nowrap}
.footer{left:0;top:1099px;width:779px;height:101px;background:var(--dark2);color:#ddd;font-size:8.5px}
.fcol{position:absolute;top:17px;list-style:none}
.fcol li{height:18.5px}
.fcol li:before{content:"» ";color:#aaa}
.fbrand{position:absolute;left:550px;top:22px;color:#fff;font-size:21px;display:flex;align-items:center;gap:7px}
.fbrand i{width:11px;height:11px;border-radius:50%;background:#bbb;display:inline-block}
.social{position:absolute;left:468px;top:50px;display:flex;flex-direction:column;gap:3px}
.social span{display:flex;align-items:center;gap:4px;font-size:7.5px;line-height:10px;color:#ddd;white-space:nowrap}
.social span i{width:9px;height:9px;background:#3a8fd4;display:inline-block}
.copy{position:absolute;right:75px;text-align:right;font-size:8.5px;white-space:nowrap}
</style>
</head>
<body>
<div class="canvas">

<header class="abs topbar">
  <div class="abs brand">winkatwheel <i></i></div>
  <nav class="abs nav">
    <a class="on">Home</a><a>Profile</a><span class="sep">|</span><a>Messages</a><span class="sep">|</span><a>Matches</a><span class="sep">|</span><a>Search</a><span class="sep">|</span><a>Support</a><span class="sep">|</span><a>My Account</a>
  </nav>
</header>

<section class="abs box life" style="left:54px;top:90px;width:138px;height:162px">
  <div class="boxhead hb">Life</div>
  <div class="abs photo" role="img" aria-label="Member profile photo" style="left:13px;top:35px;width:113px;height:63px;background:linear-gradient(135deg,#7a6a5a,#3d352e)"></div>
  <div class="abs" style="left:11px;top:107px;width:118px;height:17px;border:1px solid #ddd;border-radius:9px;font-size:8px;line-height:15px;padding-left:10px;color:#777">how are you?</div>
  <div class="abs" style="left:113px;top:108px;width:15px;height:15px;border-radius:50%;background:var(--pink);color:#fff;font-size:9px;line-height:15px;text-align:center">›</div>
  <div class="btn" style="left:15px;top:131px;width:50px;background:var(--blue2)">Profile</div>
  <div class="btn" style="left:70px;top:131px;width:44px;background:var(--orange)">Upload</div>
</section>

<section class="abs box search" style="left:54px;top:260px;width:138px;height:150px">
  <div class="boxhead hb">Search Someone</div>
  <div class="field" style="top:37px">Search Reg</div>
  <div class="field" style="top:63px">Make<span class="caret"></span></div>
  <div class="field" style="top:89px">Colour<span class="caret"></span></div>
  <div class="btn" style="left:84px;top:115px;width:44px;height:18px;line-height:18px;background:#666;font-weight:700">SEARCH</div>
</section>

<section class="abs feature" style="left:54px;top:422px;width:140px;height:152px">
  <div class="top" style="background:var(--orange2)">
    <svg width="44" height="44" viewBox="0 0 44 44" fill="none" stroke="#fff" stroke-width="4" stroke-linecap="round"><circle cx="18" cy="18" r="12"/><path d="M27 27l11 11"/></svg>
  </div>
  <h3 style="color:var(--orange2)">Find Now</h3>
  <p>Vivamus porttitor, g, purus nisi eleifend libero, a tempus libero lectus feugiat felis diam</p>
</section>

<section class="abs box favourites" style="left:54px;top:590px;width:138px;height:412px">
  <div class="boxhead hg">Your Favourite</div>
  <div class="fav" style="top:38px"><div class="photo" role="img" aria-label="Favourite member photo" style="background:linear-gradient(135deg,#b59a7a,#6d5d4a)"></div><b>Person Name</b><span style="top:17px">Age Years</span><span style="top:30px">City/Location</span></div>
  <div class="favline" style="top:92px"></div>
  <div class="fav" style="top:96px"><div class="photo" role="img" aria-label="Favourite member photo" style="background:linear-gradient(135deg,#c8875a,#5a3a28)"></div><b>Person Name</b><span style="top:17px">Age Years</span><span style="top:30px">City/Location</span></div>
  <div class="favline" style="top:150px"></div>
  <div class="fav" style="top:154px"><div class="photo" role="img" aria-label="Favourite member photo" style="background:linear-gradient(135deg,#e0b48e,#8a5a3a)"></div><b>Person Name</b><span style="top:17px">Age Years</span><span style="top:30px">City/Location</span></div>
  <div class="favline" style="top:208px"></div>
  <div class="fav" style="top:212px"><div class="photo" role="img" aria-label="Favourite member photo" style="background:linear-gradient(135deg,#d8b090,#9a4a30)"></div><b>Person Name</b><span style="top:17px">Age Years</span><span style="top:30px">City/Location</span></div>
  <div class="favline" style="top:266px"></div>
  <div class="fav" style="top:270px"><div class="photo" role="img" aria-label="Favourite member photo" style="background:linear-gradient(135deg,#e6d2bd,#a08a74)"></div><b>Person Name</b><span style="top:17px">Age Years</span><span style="top:30px">City/Location</span></div>
  <div class="favline" style="top:324px"></div>
  <div class="fav" style="top:328px"><div class="photo" role="img" aria-label="Favourite member photo" style="background:linear-gradient(135deg,#c89a78,#4a3024)"></div><b>Person Name</b><span style="top:17px">Age Years</span><span style="top:30px">City/Location</span></div>
</section>

<article class="post" style="top:86px"><div class="card"></div><div class="head pink">Nunc porta convallis</div><div class="photo" role="img" aria-label="Member photo" style="background:linear-gradient(135deg,#c9a38a,#3a2a22)"></div><p>Porttitor, g, purus nisi eleifend libero, a tempus libero lectus feugiat felis. Morbi diam mauris, viverra in, gravida eu, mattis in.</p><div class="meta"><span class="bubble"></span>Posted 2 hours ago</div></article>
<article class="post" style="top:206px"><div class="card"></div><div class="head pink">Vivamus porttitor g urus</div><div class="photo" role="img" aria-label="Member photo" style="background:linear-gradient(135deg,#d49a80,#8a2a1a)"></div><p>Porttitor, g, purus nisi eleifend libero, a tempus libero lectus feugiat felis. Morbi diam mauris, viverra in, gravida eu, mattis in.</p><div class="meta"><span class="bubble"></span>Posted 2 hours ago</div></article>
<article class="post" style="top:324px"><div class="card"></div><div class="head green">Class aptent taciti</div><div class="photo" role="img" aria-label="Member photo" style="background:linear-gradient(135deg,#c89070,#5a3a2a)"></div><p>Porttitor, g, purus nisi eleifend libero, a tempus libero lectus feugiat felis. Morbi diam mauris, viverra in, gravida eu, mattis in.</p><div class="meta"><span class="bubble"></span>Posted 2 hours ago</div></article>
<article class="post" style="top:444px"><div class="card"></div><div class="head orange">Etiam est unc venenatis</div><div class="photo" role="img" aria-label="Member photo" style="background:linear-gradient(135deg,#e8c0a0,#4a2a1e)"></div><p>Porttitor, g, purus nisi eleifend libero, a tempus libero lectus feugiat felis. Morbi diam mauris, viverra in, gravida eu, mattis in.</p><div class="meta"><span class="bubble"></span>Posted 2 hours ago</div></article>
<article class="post" style="top:563px"><div class="card"></div><div class="head orange">Phasellus felis dolor scelerisque</div><div class="photo" role="img" aria-label="Member photo" style="background:linear-gradient(135deg,#c08a68,#3a2a20)"></div><p>Porttitor, g, purus nisi eleifend libero, a tempus libero lectus feugiat felis. Morbi diam mauris, viverra in, gravida eu, mattis in.</p><div class="meta"><span class="bubble"></span>Posted 2 hours ago</div></article>
<article class="post" style="top:684px"><div class="card"></div><div class="head pink">Class aptent taciti sociosqu</div><div class="photo" role="img" aria-label="Member photo" style="background:linear-gradient(135deg,#d8b080,#6a4a2a)"></div><p>Porttitor, g, purus nisi eleifend libero, a tempus libero lectus feugiat felis. Morbi diam mauris, viverra in, gravida eu, mattis in.</p><div class="meta"><span class="bubble"></span>Posted 2 hours ago</div></article>
<article class="post" style="top:802px;left:208px"><div class="card"></div><div class="head blue">Nunc porta convallis ped</div><div class="photo" role="img" aria-label="Member photo" style="background:linear-gradient(135deg,#e0dcd8,#6a5a50)"></div><p>Porttitor, g, purus nisi eleifend libero, a tempus libero lectus feugiat felis. Morbi diam mauris, viverra in, gravida eu, mattis in.</p><div class="meta"><span class="bubble"></span>Posted 2 hours ago</div></article>
<article class="post" style="top:922px;left:208px"><div class="card"></div><div class="head green">Duis sed tellus et</div><div class="photo" role="img" aria-label="Member photo" style="background:linear-gradient(135deg,#5a8a5a,#c8a080)"></div><p>Porttitor, g, purus nisi eleifend libero, a tempus libero lectus feugiat felis. Morbi diam mauris, viverra in, gravida eu, mattis in.</p><div class="meta"><span class="bubble"></span>Posted 2 hours ago</div></article>

<div class="abs pager"><span class="lbl">View more comments</span><span class="pages"><span class="cur">1</span><span>2</span><span>3</span><span>4</span><span>5</span><span>7</span></span></div>

<section class="abs box matches" style="left:596px;top:90px;width:137px;height:426px">
  <div class="boxhead hb" style="height:28px;line-height:30px">Your Matches</div>
  <ul class="mlist">
    <li><b>WAW</b> has uploaded a new image</li><li><b>WAW</b> has uploaded a new image</li><li><b>WAW</b> has uploaded a new image</li><li><b>WAW</b> has uploaded a new image</li><li><b>WAW</b> has uploaded a new image</li><li><b>WAW</b> has uploaded a new image</li><li><b>WAW</b> has uploaded a new image</li><li><b>WAW</b> has uploaded a new image</li>
  </ul>
  <div class="match" style="left:11px;top:192px"><div class="photo" role="img" aria-label="Match photo" style="background:linear-gradient(135deg,#dfe8ef,#c08a68)"></div><em>John</em> (26)<br>New york</div>
  <div class="match" style="left:72px;top:192px"><div class="photo" role="img" aria-label="Match photo" style="background:linear-gradient(135deg,#d8e2ea,#7a5a40)"></div><em>John</em> (26)<br>New york</div>
  <div class="match dark" style="left:11px;top:284px;height:116px"><div class="photo" role="img" aria-label="Match photo" style="background:linear-gradient(135deg,#e8d0a0,#b08060)"></div><em>Karin</em> (26)<br>New york<br><span style="font-size:6.5px;line-height:12px;display:block;margin-top:2px">Duis tincidunt<br>lectus quis dui</span></div>
  <div class="match" style="left:72px;top:284px"><div class="photo" role="img" aria-label="Match photo" style="background:linear-gradient(135deg,#f0f0f0,#4a3a30)"></div><em>John</em> (26)<br>New york</div>
</section>

<section class="abs feature" style="left:597px;top:522px;width:134px;height:147px">
  <div class="top" style="background:var(--lime)">
    <svg width="48" height="44" viewBox="0 0 48 44" fill="none" stroke="#fff" stroke-width="3.5" stroke-linejoin="round"><path d="M22 38L6 22a9 9 0 0 1 16-12 9 9 0 0 1 15 6"/><circle cx="36" cy="30" r="8" fill="#fff"/><path d="M36 25v10M31 30h10" stroke="var(--lime)" stroke-width="2.5"/></svg>
  </div>
  <h3 style="color:var(--lime)">Get Connect</h3>
  <p>Vivamus porttitor, g, purus nisi eleifend libero, a tempus libero lectus feugiat felis diam</p>
</section>

<section class="abs feature" style="left:597px;top:680px;width:134px;height:148px">
  <div class="top" style="background:var(--pink)">
    <svg width="50" height="44" viewBox="0 0 50 44" fill="none" stroke="#fff" stroke-width="3.5" stroke-linejoin="round" stroke-linecap="round"><path d="M15 30H12a8 8 0 0 1 0-16 12 12 0 0 1 23-2 8 8 0 0 1 3 18h-3"/><path d="M25 40V20M18 27l7-7 7 7"/></svg>
  </div>
  <h3 style="color:var(--pink)">Sign Up</h3>
  <p>Vivamus porttitor, g, purus nisi eleifend libero, a tempus libero lectus feugiat felis diam</p>
</section>

<section class="abs feature" style="left:599px;top:839px;width:134px;height:147px">
  <div class="top" style="background:var(--cyan)">
    <svg width="46" height="46" viewBox="0 0 46 46" fill="none" stroke="#fff" stroke-width="3.5"><circle cx="23" cy="23" r="20"/><path d="M23 33L14 24a5.5 5.5 0 0 1 9-6 5.5 5.5 0 0 1 9 6z" fill="#fff"/></svg>
  </div>
  <h3 style="color:var(--cyan)">Dating</h3>
  <p>Vivamus porttitor, g, purus nisi eleifend libero, a tempus libero lectus feugiat felis diam</p>
</section>

<aside class="abs chat"><span>OPEN CHAT</span><div class="abs" style="left:10px;top:90px;width:14px;height:10px;background:#ddd;border-radius:5px"></div></aside>

<footer class="abs footer">
  <ul class="fcol" style="left:75px"><li>Home</li><li>Mobile Site</li><li>Friendbook</li><li>Chirper</li></ul>
  <ul class="fcol" style="left:168px"><li>General Conditions</li><li>Terms &amp; Conditions</li><li>Privacy Statement</li><li>Cookies Information</li></ul>
  <ul class="fcol" style="left:298px"><li>Contact us</li><li>FAQ's &amp; Help</li><li>Safe Dating Advice</li><li>Pricing Details</li></ul>
  <div class="fbrand">winkatwheel <i></i></div>
  <div class="social"><span><i></i>Friendbook</span><span><i></i>Chirper</span><span><i></i>Linkwork</span></div>
  <div class="copy" style="top:54px">Copyright © 2013 &nbsp;Wink At Wheel</div>
  <div class="copy" style="top:73px">All rights reserved.</div>
</footer>

</div>
</body>
</html>
```